Corvana Tongue Works, LLC

We need a business card that includes information about our business and conveys a reliable business that provides document translation services and interpreters for a variety of corporate and individual clients. We want to come across as professional, reliable, yet approachable. It should include the following on one side:

ESL / ENL Language Classes, Private Lessons, and Online Tutors
PLEXA Training and Testing
Translating & Interpreting Services
Contact us about Over-the-Phone Interpreting in over 200 languages
24/7/365
www.corvanatongue.example

The other side should include (555) 481-3062

Rhoda Pelling, President
482 Garnet Ave., Ste. 219
Indianapolis, IN 40917

Please add USA as part of the address. Also, please add rmpelling@corvanatongueworks.example as the e-mail address. Thank you.

Target Market(s)

Business professionals, their families, the international community

Industry/Entity Type

Business

Contact Information for Business Card

24/7/365
www.corvanatongue.example

(555) 481-3062

Rhoda Pelling, President
482 Garnet Ave., Ste. 219
Indianapolis, IN 40917
USA

Font styles to use
Sans Serif

Colors

Designer to choose colors to be used in the design.

Requirements
Must have
• See project description
• e-mail address and web address
• Phone number
Nice to have
• a globe
• physical address
Should not have
• Should not have the same color scheme as other agencies in our market in Indiana unless it is blue and black. No purple or yellow.

```html
<!DOCTYPE html>
<html lang="en">
<head>
<meta charset="utf-8">
<title>Corvana Tongue Works, LLC – Business Card</title>
<link href="https://fonts.googleapis.com/css2?family=Arimo:wght@400;700&display=swap" rel="stylesheet">
<style>
  :root {
    --brand-blue: #2596d6;
    --ink: #111111;
    --paper: #ffffff;
    --stage: #e9ebee;
    --watermark: #eef4fa;
    --map-tone: #f1f2f4;
  }
  * { box-sizing: border-box; margin: 0; padding: 0; }
  html, body { width: 1200px; height: 880px; overflow: hidden; }
  body {
    background: var(--stage);
    font-family: "Arimo", Arial, sans-serif;
    color: var(--ink);
    position: relative;
  }
  .card {
    position: absolute;
    left: 250px;
    width: 700px;
    height: 400px;
    background: var(--paper);
    border-radius: 22px;
    overflow: hidden;
    box-shadow: 0 6px 18px rgba(0,0,0,0.12);
  }
  .card--front { top: 20px; }
  .card--back { top: 460px; }
  .card__swoosh { position: absolute; inset: 0; width: 100%; height: 100%; }

  /* Front side */
  .front__watermark {
    position: absolute;
    left: 235px; top: 40px;
    width: 230px; height: 230px;
    border-radius: 50%;
    border: 16px solid var(--watermark);
    background: rgba(238,244,250,0.6);
  }
  .front__content {
    position: absolute;
    left: 0; right: 0; top: 62px;
    text-align: center;
  }
  .front__name {
    font-size: 34px;
    font-weight: 400;
    letter-spacing: 0.5px;
    text-transform: uppercase;
    margin-bottom: 14px;
  }
  .front__name .accent { color: var(--brand-blue); }
  .front__services {
    font-size: 17px;
    line-height: 1.28;
  }
  .front__services .divider { color: var(--brand-blue); }
  .front__hours {
    color: var(--brand-blue);
    font-weight: 700;
    font-size: 18px;
    margin-top: 2px;
  }
  .web {
    font-size: 17px;
    letter-spacing: 2.5px;
    margin-top: 8px;
  }
  .web .accent { color: var(--brand-blue); }

  /* Back side */
  .back__map {
    position: absolute;
    left: 140px; top: 40px;
    width: 500px; height: 270px;
    border-radius: 40%;
    background: radial-gradient(ellipse at center, var(--map-tone) 0%, rgba(241,242,244,0) 72%);
  }
  .back__brand {
    position: absolute;
    left: 205px; top: 48px;
    display: flex;
    align-items: center;
    gap: 18px;
  }
  .brand__dot {
    width: 96px; height: 96px;
    border-radius: 50%;
    background: var(--brand-blue);
    flex-shrink: 0;
  }
  .brand__name {
    font-size: 34px;
    font-weight: 400;
    line-height: 1.02;
    color: var(--ink);
  }
  .back__contact {
    position: absolute;
    left: 0; right: 0; top: 194px;
    text-align: center;
    font-size: 17px;
    line-height: 1.35;
  }
  .contact__label { color: var(--brand-blue); font-weight: 700; }
  .back__contact .web { margin-top: 6px; }
</style>
</head>
<body>

<section class="card card--front" aria-label="Business card front">
  <svg class="card__swoosh" viewBox="0 0 700 400" preserveAspectRatio="none" aria-hidden="true">
    <path d="M0 300 Q 110 370 260 400 L0 400 Z" fill="var(--brand-blue)"/>
    <path d="M700 110 Q 640 280 560 400 L700 400 Z" fill="var(--brand-blue)"/>
  </svg>
  <div class="front__watermark" aria-hidden="true"></div>
  <div class="front__content">
    <h1 class="front__name">Corvana <span class="accent">Tongue</span> Works, LLC</h1>
    <p class="front__services">ESL / ENL Language Classes <span class="divider">|</span> Private Lessons and Online Tutors</p>
    <p class="front__services">PLEXA Training and Testing</p>
    <p class="front__services">Translating &amp; Interpreting Services</p>
    <p class="front__services">Contact us about Over-the-Phone Interpreting in over 200 languages</p>
    <p class="front__hours">24/7/365</p>
    <p class="web">www.<span class="accent">corvanatongue</span>.example</p>
  </div>
</section>

<section class="card card--back" aria-label="Business card back">
  <div class="back__map" role="img" aria-label="Faint world map in the background"></div>
  <svg class="card__swoosh" viewBox="0 0 700 400" preserveAspectRatio="none" aria-hidden="true">
    <path d="M0 300 Q 90 370 210 400 L0 400 Z" fill="var(--brand-blue)"/>
    <path d="M700 140 Q 660 290 590 400 L700 400 Z" fill="var(--brand-blue)"/>
  </svg>
  <div class="back__brand">
    <span class="brand__dot" aria-hidden="true"></span>
    <span class="brand__name">Corvana<br>Tongue<br>Works LLC</span>
  </div>
  <div class="back__contact">
    <p><span class="contact__label">P:</span> (555) 481-3062</p>
    <p>Rhoda Pelling, President, 482 Garnet Ave., Ste. 219</p>
    <p>Indianapolis, IN 40917, USA</p>
    <p><span class="contact__label">E:</span> rmpelling@corvanatongueworks.example</p>
    <p class="web">www.<span class="accent">corvanatongue</span>.example</p>
  </div>
</section>

</body>
</html>
```